Dental Savings Plan - Raymond Castell DDS

We need a tri-fold brochure and 1 page flyer/poster for Dr. Raymond Castell' dental office located on Maui, Hawaii. We are offering a new "Dental Savings Plan" to patients.
I have included 3 photos, along with the office logo. You do not have to use all photos if you do not want to. We want this to catch the eyes of patients, easy for them to read and understand, and to show them that this is a much better option than dental insurance.
Please use same Hawaiian theme and colors on the office website https://www.brightcoveclinic.com .

Please also include the following to promote this new plan:

Dental Services Include
• Professional Dental Cleanings (2 per benefit year)
• Perio Maintenance Cleanings (3 per benefit year) covered at 80%
• Radiographs as needed (1 set of X-rays per benefit year)
• Doctor Examinations (2 per benefit year)
• Ozone Treatment
• BRISK Amalgam Removal
• Additional limited/emergency exam (1 per benefit year)
• Cosmetic consultation
• 15% discount on all other services (including cosmetic procedures)
• 10% discount on implants and implant crowns

Advantages of the Dental Savings Plan
1. No deductibles
2. No waiting periods
3. No claims to file
4. No frequency limitations or exclusions
5. No yearly maximum benefits
6. No pre-authorization requirements
7. No pre-existing conditions limitations
8. State of the art facility and technology
9. Immediate enrollment
10. Highest quality of care for you and your Ohana

Annual Fee
$399 first family member/individual (equivalent to $33 per month)
$349 second family member (equivalent to $29 per month)
$249 each additional family member (equivalent to $20 per month)

Provisions of the Dental Savings Plan
• May not be combined with insurance plans, discounts or promotions
• This Dental Savings Plan is not an insurance plan, but a payment arrangement provided by Raymond Castell DDS, and is not transferable to any other dental office or dental specialist
• Payment for services are due at the date of service
• This program is for you and is not transferable
• Benefits are provided for one year from the date the plan is purchased
• Must be paid in full when starting the plan
• No refunds will be provided for dues of the plan annual fee under any circumstances, including failure to schedule and maintain appointments
• If Pay Ladder is used to pay for the program and for services then only a 10% discount will be given
• To receive the full 15% discount on restorative treatment, you must schedule the appointment the day it is recommended. Any failed appointment results in the loss of the 15% discount.

Target Market(s)

Dental patients without dental insurance

Industry/Entity Type

Dental Clinic

Requirements
Must have
• My project must have the logo file to identify the dental office, Hawaiian theme, same colors as website, match style of website font, theme and colors, as well as, all the Dental Services, Advantages of the Dental Savings Plan, Annual Fee, and the Provisions of the Dental Savings Plan.

```html
<!DOCTYPE html>
<html lang="en">
<head>
<meta charset="utf-8">
<title>Dental Savings Plan – Raymond Castell DDS</title>
<link rel="stylesheet" href="https://fonts.googleapis.com/css2?family=Poppins:wght@600;700&family=Saira+Condensed:wght@600&family=PT+Sans+Narrow:wght@400;700&display=swap">
<style>
:root{
  --blue:#29a8e0;
  --blue-deep:#1d8fc4;
  --charcoal:#3a3b3f;
  --shadow-grey:#6d6e72;
  --paper:#ffffff;
  --leaf-tint:#e6efe2;
  --ink:#2b2b2e;
  --ground:#e6e6e6;
}
*{box-sizing:border-box;margin:0;padding:0}
html,body{width:1200px;height:1036px;overflow:hidden}
body{background:var(--ground);font-family:"PT Sans Narrow",sans-serif;color:var(--ink);position:relative}
.spread{position:absolute;left:12px;width:1176px;height:500px;display:flex;box-shadow:0 4px 14px rgba(0,0,0,.18)}
.spread--outside{top:12px}
.spread--inside{top:524px}
.panel{position:relative;width:392px;height:500px;overflow:hidden;background:var(--paper)}
.panel + .panel{border-left:1px solid rgba(0,0,0,.06)}
.panel svg.bands{position:absolute;inset:0;width:100%;height:100%}

/* outside: fee panel */
.fee-icon{position:absolute;left:170px;top:18px;width:52px;height:52px;border-radius:50%;background:var(--blue);display:flex;align-items:center;justify-content:center}
.fee-title{position:absolute;left:0;right:0;top:82px;text-align:center;font:700 30px "Poppins",sans-serif;color:var(--ink)}
.fee-list{position:absolute;left:40px;right:30px;top:136px;list-style:none}
.fee-list li{margin-bottom:14px;font-size:15px;line-height:1.2}
.fee-list strong{font:700 19px "Poppins",sans-serif}
.fee-list span{display:block;font-size:14px}
.patient-photo{position:absolute;left:0;right:0;bottom:0;height:180px;background:linear-gradient(120deg,#e9c7b4 0%,#f2e4dc 45%,#dfe9f1 100%)}

/* outside: contact panel */
.beach-photo{position:absolute;inset:0;background:linear-gradient(180deg,#5aa6e2 0%,#a9d3f1 38%,#2b8fc2 52%,#1fb0bd 75%,#3b7f72 100%)}
.contact-card{position:absolute;left:36px;right:36px;top:236px;padding:18px 20px;border-radius:10px;background:rgba(20,110,130,.72);color:#fff}
.contact-card ul{list-style:none}
.contact-card li{display:flex;align-items:center;gap:10px;font-size:14px;margin-bottom:8px}
.contact-card li svg{flex:none}
.social-row{display:flex;gap:12px;margin-top:12px}
.social-row span{width:30px;height:30px;border:2px solid #fff;border-radius:4px;display:flex;align-items:center;justify-content:center}

/* outside: cover */
.brand{position:absolute;left:0;right:0;top:92px;display:flex;align-items:center;justify-content:center;gap:10px}
.brand-dot{width:20px;height:20px;border-radius:50%;background:#7cc242}
.brand-name{font:600 26px "Poppins",sans-serif;color:#7cc242}
.leaf-field{position:absolute;left:0;right:0;bottom:0;height:210px;background:var(--leaf-tint);opacity:.55}
.cover-title{position:absolute;right:36px;bottom:46px;text-align:right;font:700 34px/1.1 "Poppins",sans-serif;color:var(--ink)}

/* inside panels */
.icon-badge{position:absolute;width:74px;height:74px;border-radius:50%;background:var(--blue);display:flex;align-items:center;justify-content:center;border:3px solid #fff;box-shadow:0 0 0 2px var(--blue)}
.section-title{position:absolute;font:600 25px/1.1 "Saira Condensed",sans-serif;color:var(--blue)}
.item-list{position:absolute;font-size:13px;line-height:1.18;color:var(--ink)}
.bullets{list-style:none}
.bullets li{padding-left:12px;position:relative}
.bullets li::before{content:"•";position:absolute;left:0}
.services li{margin-bottom:6px}
.numbered{list-style:decimal;padding-left:18px}
.numbered li{margin-bottom:10px}
.provisions li{font-size:12.3px;margin-bottom:6px}
.panel--advantages{background:#f4f4f4}
</style>
</head>
<body>

<section class="spread spread--outside">
  <article class="panel panel--fee">
    <svg class="bands" viewBox="0 0 392 500" aria-hidden="true">
      <polygon points="0,0 392,0 392,40 300,40 0,70" fill="var(--blue)"/>
      <polygon points="0,70 300,40 392,40 392,55 10,82" fill="var(--shadow-grey)"/>
    </svg>
    <div class="fee-icon">
      <svg width="28" height="28" viewBox="0 0 28 28" fill="none" stroke="#fff" stroke-width="2"><rect x="4" y="7" width="20" height="14" rx="2"/><line x1="4" y1="12" x2="24" y2="12"/></svg>
    </div>
    <h2 class="fee-title">Annual Fee</h2>
    <ul class="fee-list">
      <li><strong>$399</strong> first family member/individual<span>(equivalent to $33 per month)</span></li>
      <li><strong>$349</strong> second family member<span>(equivalent to $29 per month)</span></li>
      <li><strong>$249</strong> each additional family member<span>(equivalent to $20 per month)</span></li>
    </ul>
    <div class="patient-photo" role="img" aria-label="Photo of a patient during a dental checkup"></div>
  </article>

  <article class="panel panel--contact">
    <div class="beach-photo" role="img" aria-label="Photo of a tropical beach with a palm tree and turquoise sea"></div>
    <svg class="bands" viewBox="0 0 392 500" aria-hidden="true">
      <polygon points="0,0 392,0 392,30 0,70" fill="var(--blue)"/>
      <polygon points="0,470 392,440 392,500 0,500" fill="var(--blue)"/>
      <polygon points="0,455 392,428 392,440 0,470" fill="var(--charcoal)"/>
    </svg>
    <div class="contact-card">
      <ul>
        <li><svg width="16" height="16" viewBox="0 0 16 16" fill="none" stroke="#fff" stroke-width="1.5"><path d="M4 2l2 3-1.5 1.5a8 8 0 0 0 5 5L11 10l3 2-1.5 2.5C7 14 2 9 1.5 3.5z"/></svg>808-555-0172</li>
        <li><svg width="16" height="16" viewBox="0 0 16 16" fill="none" stroke="#fff" stroke-width="1.5"><rect x="1.5" y="3.5" width="13" height="9" rx="1"/><path d="M2 4l6 5 6-5"/></svg>hello@brightcoveclinic.com</li>
        <li><svg width="16" height="16" viewBox="0 0 16 16" fill="none" stroke="#fff" stroke-width="1.5"><circle cx="8" cy="8" r="6.5"/><path d="M1.5 8h13M8 1.5c3 3 3 10 0 13M8 1.5c-3 3-3 10 0 13"/></svg>www.brightcoveclinic.com</li>
        <li><svg width="16" height="16" viewBox="0 0 16 16" fill="none" stroke="#fff" stroke-width="1.5"><path d="M8 15s5-5 5-9a5 5 0 0 0-10 0c0 4 5 9 5 9z"/><circle cx="8" cy="6" r="1.8"/></svg>415 Coral Reef Way # 12, Lanakai, HI 96700</li>
      </ul>
      <div class="social-row">
        <span></span><span></span>
        <span><svg width="14" height="16" viewBox="0 0 16 16" fill="none" stroke="#fff" stroke-width="1.6"><path d="M8 15s5-5 5-9a5 5 0 0 0-10 0c0 4 5 9 5 9z"/><circle cx="8" cy="6" r="1.8"/></svg></span>
      </div>
    </div>
  </article>

  <article class="panel panel--cover">
    <svg class="bands" viewBox="0 0 392 500" aria-hidden="true">
      <rect width="392" height="240" fill="var(--charcoal)"/>
      <polygon points="0,240 392,190 392,250 0,300" fill="var(--blue)"/>
      <polygon points="0,300 392,250 392,290 0,330" fill="var(--blue-deep)" opacity=".6"/>
    </svg>
    <div class="brand"><span class="brand-dot"></span><span class="brand-name">Raymond Castell DDS</span></div>
    <div class="leaf-field" role="img" aria-label="Faint tropical leaf pattern"></div>
    <h1 class="cover-title">Dental<br>Savings Plan</h1>
  </article>
</section>

<section class="spread spread--inside">
  <article class="panel panel--services">
    <svg class="bands" viewBox="0 0 392 500" aria-hidden="true">
      <polygon points="0,0 392,0 392,20 30,20 0,60" fill="var(--blue)"/>
      <polygon points="0,60 30,20 40,20 6,70 0,74" fill="var(--shadow-grey)"/>
      <rect y="482" width="392" height="18" fill="var(--charcoal)"/>
    </svg>
    <div class="icon-badge" style="left:159px;top:28px">
      <svg width="40" height="40" viewBox="0 0 40 40" fill="none" stroke="#fff" stroke-width="2"><path d="M10 8v16h16l4 8M10 24l-2 10M14 14h10"/><circle cx="28" cy="10" r="3"/></svg>
    </div>
    <h2 class="section-title" style="left:24px;top:114px">Dental Services Include</h2>
    <ul class="item-list bullets services" style="left:24px;right:20px;top:150px">
      <li>Professional Dental Cleanings<br>(2 per benefit year)</li>
      <li>Perio Maintenance Cleanings<br>(3 per benefit year) covered at 80%</li>
      <li>Radiographs as needed<br>(1 set of X-rays per benefit year)</li>
      <li>Doctor Examinations<br>(2 per benefit year)</li>
      <li>Ozone Treatment</li>
      <li>BRISK Amalgam Removal</li>
      <li>Additional limited/emergency exam<br>(1 per benefit year)</li>
      <li>Cosmetic consultation</li>
      <li>15% discount on all other services<br>(including cosmetic procedures)</li>
      <li>10% discount on implants and implant crowns</li>
    </ul>
  </article>

  <article class="panel panel--advantages">
    <svg class="bands" viewBox="0 0 392 500" aria-hidden="true">
      <polygon points="0,0 392,0 392,10 0,40" fill="var(--blue)"/>
      <rect y="482" width="392" height="18" fill="var(--charcoal)"/>
    </svg>
    <div class="icon-badge" style="left:159px;top:40px">
      <svg width="36" height="40" viewBox="0 0 36 40" fill="none" stroke="#fff" stroke-width="2"><path d="M18 6c-4-3-13-3-13 7 0 8 3 10 4 16s2 8 4 8 2-9 5-9 3 9 5 9 3-2 4-8 4-8 4-16c0-10-9-10-13-7z"/></svg>
    </div>
    <h2 class="section-title" style="left:24px;top:128px">Advantages of the<br>Dental Savings Plan</h2>
    <ol class="item-list numbered" style="left:28px;right:20px;top:194px">
      <li>No deductibles</li>
      <li>No waiting periods</li>
      <li>No claims to file</li>
      <li>No frequency limitations or exclusions</li>
      <li>No yearly maximum benefits</li>
      <li>No pre-authorization requirements</li>
      <li>No pre-existing conditions limitations</li>
      <li>State of the art facility and technology</li>
      <li>Immediate enrollment</li>
      <li>Highest quality of care for you and your Ohana</li>
    </ol>
  </article>

  <article class="panel panel--provisions">
    <svg class="bands" viewBox="0 0 392 500" aria-hidden="true">
      <polygon points="0,470 392,440 392,500 0,500" fill="var(--charcoal)"/>
    </svg>
    <div class="icon-badge" style="left:292px;top:14px">
      <svg width="40" height="40" viewBox="0 0 40 40" fill="none" stroke="#fff" stroke-width="2"><path d="M16 6c-3-2-11-2-11 6 0 7 3 9 3 14s2 7 3 7 2-8 4-8"/><circle cx="24" cy="20" r="7"/><line x1="29" y1="25" x2="35" y2="32"/></svg>
    </div>
    <h2 class="section-title" style="left:20px;top:26px">Provisions<br>of the Dental<br>Savings Plan</h2>
    <ul class="item-list bullets provisions" style="left:20px;right:22px;top:118px">
      <li>May not be combined with insurance plans, discounts or promotions</li>
      <li>This Dental Savings Plan is not an insurance plan, but a payment arrangement provided by Raymond Castell DDS, and is not transferable to any other dental office or dental specialist</li>
      <li>Payment for services are due at the date of service</li>
      <li>This program is for you and is not transferable</li>
      <li>Benefits are provided for one year from the date the plan is purchased</li>
      <li>Must be paid in full when starting the plan</li>
      <li>No refunds will be provided for dues of the plan annual fee under any circumstances, including failure to schedule and maintain appointments</li>
      <li>If Pay Ladder is used to pay for the program and for services then only a 10% discount will be given</li>
      <li>To receive the full 15% discount on restorative treatment, you must schedule the appointment the day it is recommended. Any failed appointment results in the loss of the 15% discount.</li>
    </ul>
  </article>
</section>

</body>
</html>
```